Business Recognition Design

We need a design for a recognition to be given to business leaders in our community.
The recognition shall be made on a brass plaque on wood panel background (picture attached, please use it as a background), and all drawing must be in vectors and only one color (black).
It should also have a logo on the top and signature on the right bottom.
The text is enclosed in DOC file.
Updates

Reason: just to be able to find the best solution

Reason: None of the suggestion is good enough. Logo in general is too big in comparison with the rest of the plate.

Industry/Entity Type

Business

Requirements
Must have
• - standard Windows font (or possibility to install the same font on Windows), as the name on the recognition shall be printed in the same font
Nice to have
• - some graphic element (in curves) representing achievements in business
- should look great :)

```html
<!DOCTYPE html>
<html lang="de">
<head>
<meta charset="utf-8">
<title>Auszeichnung – Wertanker</title>
<link rel="stylesheet" href="https://fonts.googleapis.com/css2?family=Arimo:wght@400;700&display=swap">
<style>
  :root {
    --backdrop: #3b3b3d;
    --wood-dark: #4a2f1a;
    --wood-mid: #6e4a2b;
    --wood-light: #80593a;
    --brass-light: #f6dc6a;
    --brass-mid: #e3bd3c;
    --brass-deep: #c49a24;
    --engrave: #1d1a12;
    --ornament: #b58d22;
    --screw-light: #fbe38a;
    --screw-dark: #9a7416;
  }
  * { margin: 0; padding: 0; box-sizing: border-box; }
  html, body {
    width: 1200px;
    height: 832px;
    overflow: hidden;
    background: var(--backdrop);
    font-family: "Arimo", Arial, sans-serif;
    color: var(--engrave);
  }
  .plaque {
    position: absolute;
    left: 110px;
    top: 38px;
    width: 980px;
    height: 756px;
    border-radius: 6px;
    background: linear-gradient(90deg, var(--wood-dark), var(--wood-mid) 30%, var(--wood-light) 55%, var(--wood-mid) 80%, var(--wood-dark));
    box-shadow: inset 0 0 0 3px rgba(0,0,0,0.25);
  }
  .brass-plate {
    position: absolute;
    left: 34px;
    top: 26px;
    width: 912px;
    height: 702px;
    background: linear-gradient(160deg, var(--brass-light), var(--brass-mid) 45%, var(--brass-deep) 80%, var(--brass-mid));
    box-shadow: 0 2px 4px rgba(0,0,0,0.45);
  }
  .frame {
    position: absolute;
    left: 63px;
    top: 56px;
    width: 786px;
    height: 586px;
    border: 2px solid var(--engrave);
  }
  .frame::after {
    content: "";
    position: absolute;
    inset: 6px;
    border: 1.5px solid var(--engrave);
  }
  .corner-ornament {
    position: absolute;
    width: 54px;
    height: 54px;
    background: var(--ornament);
  }
  .corner-ornament.top-left { left: 52px; top: 45px; }
  .corner-ornament.top-right { right: 52px; top: 45px; }
  .corner-ornament.bottom-left { left: 52px; bottom: 45px; }
  .corner-ornament.bottom-right { right: 52px; bottom: 45px; }
  .screw {
    position: absolute;
    width: 22px;
    height: 22px;
    border-radius: 50%;
    background: radial-gradient(circle at 35% 35%, var(--screw-light), var(--brass-deep) 60%, var(--screw-dark));
    box-shadow: 0 1px 2px rgba(0,0,0,0.5);
  }
  .screw.tl { left: 26px; top: 31px; }
  .screw.tr { right: 26px; top: 31px; }
  .screw.bl { left: 26px; bottom: 31px; }
  .screw.br { right: 26px; bottom: 31px; }
  .line {
    position: absolute;
    left: 0;
    width: 100%;
    text-align: center;
    white-space: nowrap;
  }
  .brand-name { top: 124px; font-size: 37px; font-weight: 700; letter-spacing: -0.5px; }
  .award-title { top: 190px; font-size: 66px; font-weight: 400; letter-spacing: 1px; }
  .award-reason { font-size: 32px; font-weight: 700; }
  .award-reason.first { top: 272px; }
  .award-reason.second { top: 314px; }
  .award-for { top: 363px; font-size: 22px; }
  .recipient { top: 391px; font-size: 29px; font-weight: 700; }
  .citation { font-size: 20px; }
  .citation.first { top: 433px; }
  .citation.second { top: 463px; }
  .citation.third { top: 493px; }
  .citation strong { font-size: 22px; }
  .citation small { font-size: 12px; font-weight: 700; }
  .place-date, .signatory {
    position: absolute;
    top: 612px;
    font-size: 21px;
    white-space: nowrap;
    transform: translateX(-50%);
  }
  .place-date { left: 335px; }
  .signatory { left: 622px; }
</style>
</head>
<body>
  <main class="plaque">
    <section class="brass-plate">
      <span class="screw tl"></span>
      <span class="screw tr"></span>
      <span class="screw bl"></span>
      <span class="screw br"></span>

      <div class="frame"></div>
      <div class="corner-ornament top-left" role="img" aria-label="Engraved corner knot ornament"></div>
      <div class="corner-ornament top-right" role="img" aria-label="Engraved corner knot ornament"></div>
      <div class="corner-ornament bottom-left" role="img" aria-label="Engraved corner knot ornament"></div>
      <div class="corner-ornament bottom-right" role="img" aria-label="Engraved corner knot ornament"></div>

      <p class="line brand-name">Wertanker</p>
      <h1 class="line award-title">AUSZEICHNUNG</h1>
      <p class="line award-reason first">als herausragendster Unternehmer</p>
      <p class="line award-reason second">Deutschlands 2013</p>
      <p class="line award-for">für</p>
      <p class="line recipient">Herrn Dipl.-Kfm. Max Muster</p>
      <p class="line citation first">Unter der Leitung von <strong>Herr Dipl.-Kfm.</strong> <small>Max Muster</small></p>
      <p class="line citation second">hat sich die FIRMA GmbH im Jahr 2013 unter den ersten 5% der</p>
      <p class="line citation third">größten deutschen Wirtschaftsunternehmen platziert.</p>

      <p class="place-date">Gilching, 20. Juni 2013</p>
      <p class="signatory">Lena Brandt</p>
    </section>
  </main>
</body>
</html>
```